TEBSIRK HOA Portal Site for Public

Clean up and organize current website; need website to look good and functional; this is a HOA (homeowner association management) website where homeowners can login and pay their bill, general information about a HOA, monthly newsletter page.
Competitors:
https://quillmarsh.example/
https://dorvinpalms.example/
https://www.kelbrookhomes.example/nevada
http://www.tpw-hoa.example/

Target Market(s)

homeowners

Industry/Entity Type

Real Estate

Coding

Coded - Design and coding required

Number of Pages Required

5+ page

Font styles to use
Serif

Colors
0292cd
33a6d7
e667a6
e34297

Requirements
Must have
• login to pay
• services page
• contact us
• order resale package
Nice to have
• page why an HOA would contract us

```html
<!DOCTYPE html>
<html lang="en">
<head>
<meta charset="utf-8">
<title>TEBSIRK HOA</title>
<link href="https://fonts.googleapis.com/css2?family=Cinzel:wght@700&family=Nunito+Sans:wght@300;400&display=swap" rel="stylesheet">
<style>
:root{
  --blue:#0292cd;
  --blue-light:#33a6d7;
  --pink:#e667a6;
  --pink-deep:#e34297;
  --ink:#111111;
  --text:#555555;
  --heading:#1a1a1a;
  --white:#ffffff;
}
*{margin:0;padding:0;box-sizing:border-box}
html,body{width:1200px;height:2552px;overflow:hidden;background:var(--white)}
body{position:relative;font-family:"Nunito Sans",sans-serif;color:var(--text)}
.abs{position:absolute}
.serif{font-family:"Cinzel",serif;font-weight:700}

/* header */
.site-header{left:0;top:0;width:1200px;height:94px}
.brand{left:80px;top:30px;font-size:27px;color:var(--blue);letter-spacing:.5px}
.main-nav{left:351px;top:39px;display:flex;gap:22px;font-size:12.5px;letter-spacing:.3px;color:#444}
.login-btn{left:1019px;top:24px;width:104px;height:47px;background:linear-gradient(180deg,var(--pink),var(--pink-deep));color:var(--white);font-size:16px;display:flex;align-items:center;justify-content:center}

/* hero */
.hero{left:0;top:94px;width:1200px;height:552px;background:linear-gradient(180deg,#5f6fae 0%,#aab6d4 22%,#4d5a44 32%,#6c6650 60%,#3f4a35 100%)}
.hero-line{left:50%;transform:translateX(-50%);background:rgba(10,10,10,.82);color:var(--white);font-size:32px;padding:0 13px;height:57px;display:flex;align-items:center;white-space:nowrap;letter-spacing:.5px}

/* section headings */
.section-title{left:0;width:1200px;text-align:center;font-size:35px;color:var(--ink)}
.section-intro{left:250px;width:700px;text-align:center;font-size:13.5px;line-height:25px}

/* services */
.services-photo{left:77px;top:867px;width:458px;height:323px;background:linear-gradient(135deg,#8a6a4e,#c7a27a 45%,#2e4a7a 80%,#d8d2c6)}
.service{left:615px;width:510px}
.service-dash{position:absolute;left:0;top:12px;width:17px;height:3px;background:var(--blue)}
.service-title{margin-left:33px;font-size:19.5px;line-height:31px;color:#333}
.service-text{margin-left:33px;margin-top:14px;font-size:13.5px;line-height:25px}

/* offer */
.offer-photo{left:0;top:1323px;width:1200px;height:417px;background:linear-gradient(180deg,#8a8392 0%,#d4a49a 35%,#5e6a6c 65%,#2f4a2a 100%)}
.offer-card{left:656px;top:1292px;width:417px;height:479px;background:linear-gradient(180deg,var(--blue-light),var(--blue));color:var(--white);padding:55px 30px 0 37px}
.offer-title{font-size:30px;letter-spacing:.5px}
.offer-list{list-style:none;margin-top:16px;font-size:13.5px;line-height:25px}
.offer-list li{margin-bottom:14px}
.read-more{display:flex;align-items:center;gap:12px;font-size:15px;text-decoration:underline;margin-top:2px}

/* testimonials */
.testimonial{width:470px}
.testimonial-text{font-size:13.5px;line-height:25px}
.avatar{position:absolute;left:0;top:100px;width:73px;height:73px;border-radius:50%;border:2px solid var(--blue);background:radial-gradient(circle at 50% 45%,#d9b48a,#9c7a5c 70%)}
.testimonial-name{position:absolute;left:105px;top:114px;font-size:15px;color:#222}
.testimonial-role{position:absolute;left:105px;top:148px;font-size:13px;color:#333}

/* newsletter */
.newsletter{left:0;top:2156px;width:1200px;height:157px;background:linear-gradient(180deg,var(--blue-light),var(--blue))}
.newsletter-title{left:81px;top:42px;font-size:30px;color:var(--white)}
.newsletter-sub{left:79px;top:98px;font-size:15.5px;color:var(--white)}
.newsletter-form{left:654px;top:53px;width:469px;height:52px;border:1px solid var(--white);display:flex}
.newsletter-input{flex:1;color:var(--white);font-size:13px;padding-left:19px;display:flex;align-items:center}
.subscribe-btn{width:146px;background:linear-gradient(180deg,var(--pink),var(--pink-deep));color:var(--white);font-size:16px;display:flex;align-items:center;justify-content:center}

/* footer */
.site-footer{left:0;top:2313px;width:1200px;height:239px;background:var(--ink);color:var(--white)}
.footer-brand{left:0;width:1200px;top:59px;text-align:center;font-size:30px}
.footer-nav{left:0;width:1200px;top:122px;display:flex;justify-content:center;gap:24px;font-size:13.5px}
.footer-nav .sep{opacity:.8}
.copyright{left:0;width:1200px;top:172px;text-align:center;font-size:13.5px}
</style>
</head>
<body>

<header class="site-header abs">
  <div class="brand abs serif">TEBSIRK HOA</div>
  <nav class="main-nav abs">
    <span>HOME</span><span>SERVICES</span><span>ORDER RESALE PACKAGE</span><span>WHY AN HAO WOULD CONTRACT US</span><span>CONTACT</span>
  </nav>
  <div class="login-btn abs serif">LOGIN</div>
</header>

<section class="hero abs" role="img" aria-label="Aerial photograph of a suburban housing community with hills under a blue sky"></section>
<div class="hero-line abs serif" style="top:316px">LOREM IPSUM IS SIMPLY DUMMY.</div>
<div class="hero-line abs serif" style="top:389px">DUMMY TEXT OF TYPESETTING AND PRINT</div>

<h2 class="section-title abs serif" style="top:694px">OUR SERVICES</h2>
<p class="section-intro abs" style="top:754px">Lorem ipsum dolor sit amet, consectetur adipiscing elit, sed do eiusmod tempor incididunt ut labore et dolore magna aliqua. Ut enim ad minim vm, quis nostrud exercitation ullamco laboris nisi ut.</p>

<div class="services-photo abs" role="img" aria-label="Photograph of a couple reviewing documents with an association manager"></div>
<div class="service abs" style="top:885px">
  <span class="service-dash"></span>
  <h3 class="service-title" style="font-weight:400">Association Management Services</h3>
  <p class="service-text">Lorem ipsum dolor sit amet, consectetur adipiscing elit, sed do eiusmod tempor incididunt ut labore et dolore magna aliqua. Ut enim ad minim vm, quis nostrud exercitation ullamco laboris nisi ut aliquip ex ea</p>
</div>
<div class="service abs" style="top:1030px">
  <span class="service-dash"></span>
  <h3 class="service-title" style="font-weight:400">TEBSIRK manages communities throughout Southern Nevada</h3>
  <p class="service-text">Lorem ipsum dolor sit amet, consectetur adipiscing elit, sed do eiusmod tempor incididunt ut labore et dolore magna aliqua. Ut enim ad minim vm, quis nostrud exercitation ullamco laboris nisi ut aliquip ex ea</p>
</div>

<div class="offer-photo abs" role="img" aria-label="Photograph of a city skyline and bridge over a river at sunset"></div>
<div class="offer-card abs">
  <h2 class="offer-title serif">WHAT WE OFFER</h2>
  <ul class="offer-list">
    <li>Accessible, licensed Association Managers</li>
    <li>24 hour Web site access: online account information</li>
    <li>24 hour emergency service</li>
    <li>Provide monthly financial reports to the Board of Directors</li>
    <li>Read, study and understand all governing documents of the Association. Correspond with members in violation of the CC&amp;Rs, By-laws...</li>
  </ul>
  <div class="read-more serif">READ MORE
    <svg width="28" height="12" viewBox="0 0 28 12" aria-hidden="true"><path d="M0 6H26M20 1l6 5-6 5" fill="none" stroke="#fff" stroke-width="1.5"/></svg>
  </div>
</div>

<h2 class="section-title abs serif" style="top:1825px">CLIENT TESTIMONIALS</h2>
<div class="testimonial abs" style="left:79px;top:1903px">
  <p class="testimonial-text">Lorem ipsum dolor sit amet, consectetur adipiscing elit, sed do eiusmod tempor incididunt ut labore et dolore magna aliqua. Ut enim ad minim vm, quis nostrud exercitation ullamco laboris nisi ut aliquip ex ea</p>
  <div class="avatar" role="img" aria-label="Client portrait photo"></div>
  <div class="testimonial-name">- NAME SURNAME</div>
  <div class="testimonial-role">Lorem ipsum dolor.</div>
</div>
<div class="testimonial abs" style="left:625px;top:1903px">
  <p class="testimonial-text">Lorem ipsum dolor sit amet, consectetur adipiscing elit, sed do eiusmod tempor incididunt ut labore et dolore magna aliqua. Ut enim ad minim vm, quis nostrud exercitation ullamco laboris nisi ut aliquip ex ea</p>
  <div class="avatar" role="img" aria-label="Client portrait photo"></div>
  <div class="testimonial-name">- NAME SURNAME</div>
  <div class="testimonial-role">Lorem ipsum dolor.</div>
</div>

<section class="newsletter abs">
  <h2 class="newsletter-title abs serif">NEWSLETTER</h2>
  <p class="newsletter-sub abs">Subscribe to our newsletter to get latest Info and updates.</p>
  <div class="newsletter-form abs">
    <div class="newsletter-input">Enter your email</div>
    <div class="subscribe-btn serif">SUBSCRIBE</div>
  </div>
</section>

<footer class="site-footer abs">
  <div class="footer-brand abs serif">TEBSIRK HOA</div>
  <nav class="footer-nav abs">
    <span>Home</span><span class="sep">I</span><span>Services We Provide</span><span class="sep">I</span><span>Order resale package</span><span class="sep">I</span><span>Why an HOA would contract us</span><span class="sep">I</span><span>Contact</span>
  </nav>
  <p class="copyright abs">©TEBSIRK HOA- 2019. All Rights Reserved.</p>
</footer>

</body>
</html>
```